Harborline Renewal Business Card Design

Professional and clean design. The design colors should flow with the logo. Two-sided card with the website on the back which is:

www.HarborlineRenewal.example.

"Specializing in Water Damage Restoration"

On the front I need the name, email, phone, and logo.

Name: Darnell Quisby
Email: Darnell@HarborlineRenewal.example
Phone: 555-318-2046 for now

I only have the Preview and Thumbnail right now but should have the source files uploaded within a day or two.

Target Market(s)

Flood victims, home owners with water damage from busted pipes etc...

Industry/Entity Type

Business

Contact Information for Business Card

Name: Darnell Quisby

Font styles to use
Serif
Sans Serif

Requirements
Must have
• Business Card Details Info

```html
<!DOCTYPE html>
<html lang="en">
<head>
<meta charset="utf-8">
<title>Harborline Renewal Business Card</title>
<link href="https://fonts.googleapis.com/css2?family=Marcellus+SC&family=Source+Sans+3:wght@400&display=swap" rel="stylesheet">
<style>
  :root {
    --page: #ecebe8;
    --card-white: #ffffff;
    --brand-blue: #2f8fd0;
    --deep-blue: #2a93d5;
    --sky-blue: #55bfee;
    --stripe-blue: #5fc3f0;
    --ink: #4a4a4a;
    --rule: #b8b8b8;
    --mark-dark: #1b1b1b;
  }
  * { margin: 0; padding: 0; box-sizing: border-box; }
  html, body { width: 1200px; height: 1189px; overflow: hidden; background: var(--page); }
  .canvas { position: relative; width: 1200px; height: 1189px; }

  .card {
    position: absolute;
    width: 907px;
    height: 517px;
    border-radius: 42px;
    overflow: hidden;
  }
  .card-front { left: 40px; top: 64px; background: var(--card-white); }
  .card-back { left: 231px; top: 631px; background: var(--sky-blue); }

  .front-waves { position: absolute; left: 0; top: 0; width: 907px; height: 517px; }

  .brand-block {
    position: absolute;
    left: 40px;
    top: 60px;
    width: 380px;
    text-align: center;
  }
  .brand-dot {
    display: block;
    width: 104px;
    height: 104px;
    margin: 0 auto 18px;
    border-radius: 50%;
    background: var(--brand-blue);
  }
  .brand-name {
    font-family: "Marcellus SC", serif;
    color: var(--brand-blue);
    font-size: 50px;
    line-height: 1;
    letter-spacing: 1px;
  }
  .brand-sub {
    font-family: "Marcellus SC", serif;
    color: var(--brand-blue);
    font-size: 24px;
    letter-spacing: 5px;
    margin-top: 6px;
    display: flex;
    align-items: center;
    justify-content: center;
    gap: 10px;
  }
  .brand-sub::before, .brand-sub::after {
    content: "";
    width: 46px;
    height: 2px;
    background: var(--brand-blue);
  }

  .divider {
    position: absolute;
    left: 436px;
    top: 85px;
    width: 2px;
    height: 198px;
    background: var(--rule);
  }

  .contact-block { position: absolute; left: 464px; top: 80px; }
  .person-name {
    font-family: "Marcellus SC", serif;
    color: var(--brand-blue);
    font-size: 34px;
    line-height: 1.1;
    letter-spacing: 1px;
  }
  .person-title {
    font-family: "Marcellus SC", serif;
    color: var(--ink);
    font-size: 29px;
    letter-spacing: 2px;
    line-height: 1.1;
  }
  .contact-list { list-style: none; margin-top: 34px; }
  .contact-list li {
    font-family: "Source Sans 3", sans-serif;
    color: var(--ink);
    font-size: 23px;
    line-height: 35px;
    display: flex;
    align-items: center;
    gap: 10px;
  }
  .contact-icon { width: 20px; height: 20px; flex: none; }

  .tagline {
    position: absolute;
    left: 0;
    width: 100%;
    text-align: center;
    font-family: "Marcellus SC", serif;
    font-size: 25px;
    letter-spacing: 1px;
  }
  .card-front .tagline { top: 456px; color: var(--card-white); }
  .card-back .tagline { top: 403px; color: var(--mark-dark); }

  .back-brand {
    position: absolute;
    left: 0;
    top: 150px;
    width: 100%;
    text-align: center;
    font-family: "Marcellus SC", serif;
    color: var(--mark-dark);
    font-size: 62px;
    line-height: 1.1;
    letter-spacing: 2px;
  }
  .back-website {
    position: absolute;
    left: 0;
    top: 448px;
    width: 100%;
    text-align: center;
    font-family: "Source Sans 3", sans-serif;
    color: var(--mark-dark);
    font-size: 23px;
    line-height: 1.2;
  }
</style>
</head>
<body>
<main class="canvas">

  <section class="card card-front" aria-label="Card front">
    <svg class="front-waves" viewBox="0 0 907 517" aria-hidden="true">
      <path d="M0 300 C 70 380, 200 415, 360 405 C 560 392, 740 330, 907 318 L907 517 L0 517 Z" fill="var(--deep-blue)"/>
      <path d="M0 292 C 80 372, 210 398, 370 390 C 560 378, 740 320, 907 305" fill="none" stroke="var(--stripe-blue)" stroke-width="7"/>
      <path d="M0 318 C 60 375, 190 402, 350 398" fill="none" stroke="var(--card-white)" stroke-width="3"/>
      <path d="M520 372 C 660 340, 790 318, 907 312" fill="none" stroke="var(--card-white)" stroke-width="3"/>
    </svg>

    <div class="brand-block">
      <span class="brand-dot"></span>
      <div class="brand-name">HARBORLINE</div>
      <div class="brand-sub">RENEWAL</div>
    </div>

    <div class="divider"></div>

    <div class="contact-block">
      <div class="person-name">Darnell Quisby</div>
      <div class="person-title">Title</div>
      <ul class="contact-list">
        <li>
          <svg class="contact-icon" viewBox="0 0 20 20" aria-hidden="true"><circle cx="10" cy="10" r="8.5" fill="none" stroke="var(--brand-blue)" stroke-width="1.6"/><path d="M7 5.5 L9 8 L8 9.5 C8.8 11 9.8 12 11 12.5 L12.5 11.5 L14.5 13.5 L13 15 C9.5 14.5 6 11 5.5 7 Z" fill="var(--brand-blue)"/></svg>
          555-318-2046
        </li>
        <li>
          <svg class="contact-icon" viewBox="0 0 20 20" aria-hidden="true"><path d="M2 8 L10 3 L18 8 L18 17 L2 17 Z" fill="var(--brand-blue)"/><path d="M2 8 L10 13 L18 8" fill="none" stroke="var(--card-white)" stroke-width="1.4"/></svg>
          Darnell@HarborlineRenewal.example
        </li>
        <li>
          <svg class="contact-icon" viewBox="0 0 20 20" aria-hidden="true"><g fill="none" stroke="var(--brand-blue)" stroke-width="1.5"><circle cx="10" cy="10" r="8.5"/><ellipse cx="10" cy="10" rx="3.8" ry="8.5"/><path d="M1.5 10 H18.5 M3 5.5 H17 M3 14.5 H17"/></g></svg>
          www.HarborlineRenewal.example
        </li>
      </ul>
    </div>

    <div class="tagline">Specializing in Water Damage Restoration</div>
  </section>

  <section class="card card-back" aria-label="Card back">
    <div class="back-brand">HARBORLINE<br>RENEWAL</div>
    <div class="tagline">Specializing in Water Damage Restoration</div>
    <div class="back-website">www.HarborlineRenewal.example</div>
  </section>

</main>
</body>
</html>
```